BRIGHT RIVER POWER.

I'd like my business logo.
contact name: Dennis Halvorsen
phone:0438759164
email: info@brightriverpower.net.au
website: www.brightriverpower.net.au

services:
solar
battery storage
LED lighting
energy saving solutions
general electrical
I'd like the design to look professional

Target Market(s)

Everyone

Industry/Entity Type

Business

Contact Information for Business Card

as described above

Requirements
Must have
• Id like the colours and the design to work well with my logo.

```html
<!DOCTYPE html>
<html lang="en">
<head>
<meta charset="utf-8">
<title>Bright River Power – Business Card</title>
<link href="https://fonts.googleapis.com/css2?family=Source+Sans+3:wght@400;600;700&display=swap" rel="stylesheet">
<style>
  :root {
    --backdrop: #3a3a3a;
    --card-white: #ffffff;
    --card-black: #000000;
    --green: #6abf4b;
    --green-light: #8dc63f;
    --green-deep: #4caf50;
    --sun: #f7a81b;
    --ink: #222222;
    --paper-text: #ffffff;
  }
  * { margin: 0; padding: 0; box-sizing: border-box; }
  html, body {
    width: 1200px; height: 900px; overflow: hidden;
    background: var(--backdrop);
    font-family: "Source Sans 3", "Myriad Pro", sans-serif;
  }
  .card {
    position: absolute; top: 170px;
    width: 347px; height: 561px;
    text-align: center;
    box-shadow: 0 2px 6px rgba(0,0,0,0.35);
  }
  .card--front { left: 259px; background: var(--card-white); }
  .card--back { left: 631px; background: var(--card-black); }

  .band { position: absolute; left: 102px; width: 143px; height: 30px; }
  .band--top { top: 0; }
  .band--bottom { bottom: 0; height: 28px; }

  .brand-mark {
    position: absolute; left: 50%; transform: translateX(-50%);
    border-radius: 50%; background: var(--sun);
  }
  .card--front .brand-mark { top: 95px; width: 90px; height: 90px; }
  .card--back .brand-mark { top: 70px; width: 90px; height: 90px; }

  .brand-name {
    position: absolute; left: 0; right: 0;
    font-weight: 700; color: var(--green);
    letter-spacing: 0.04em; line-height: 1.05;
  }
  .card--front .brand-name { top: 205px; font-size: 24px; }
  .card--back .brand-name { top: 190px; font-size: 40px; }

  .contact-name {
    position: absolute; top: 340px; left: 0; right: 0;
    font-size: 22px; font-weight: 600; color: var(--green);
  }
  .contact-details {
    position: absolute; top: 413px; left: 0; right: 0;
    list-style: none; font-size: 15.5px; line-height: 20px; color: var(--ink);
  }

  .services-title {
    position: absolute; top: 386px; left: 0; right: 0;
    font-size: 27px; font-weight: 400; color: var(--green-light);
    letter-spacing: 0.01em;
  }
  .services {
    position: absolute; top: 430px; left: 0; right: 0;
    list-style: none; font-size: 16px; line-height: 20.5px; color: var(--paper-text);
  }
</style>
</head>
<body>
  <section class="card card--front">
    <svg class="band band--top" viewBox="0 0 143 30" preserveAspectRatio="none" aria-hidden="true">
      <defs>
        <linearGradient id="bandTop" x1="0" y1="0" x2="0" y2="1">
          <stop offset="0" stop-color="#8dc63f"/>
          <stop offset="1" stop-color="#4caf50"/>
        </linearGradient>
      </defs>
      <path d="M0 0 H143 V30 Q71.5 14 0 30 Z" fill="url(#bandTop)"/>
    </svg>

    <div class="brand-mark" aria-hidden="true"></div>
    <div class="brand-name">BRIGHT RIVER POWER</div>

    <p class="contact-name">Dennis Halvorsen</p>
    <ul class="contact-details">
      <li>0438759164</li>
      <li>info@brightriverpower.net.au</li>
      <li>www.brightriverpower.net.au</li>
    </ul>

    <svg class="band band--bottom" viewBox="0 0 143 28" preserveAspectRatio="none" aria-hidden="true">
      <defs>
        <linearGradient id="bandBottom" x1="0" y1="0" x2="0" y2="1">
          <stop offset="0" stop-color="#8dc63f"/>
          <stop offset="1" stop-color="#4caf50"/>
        </linearGradient>
      </defs>
      <path d="M0 0 Q71.5 14 143 0 V28 H0 Z" fill="url(#bandBottom)"/>
    </svg>
  </section>

  <section class="card card--back">
    <div class="brand-mark" aria-hidden="true"></div>
    <div class="brand-name">BRIGHT RIVER<br>POWER</div>

    <h2 class="services-title">WHAT I DO</h2>
    <ul class="services">
      <li>Solar</li>
      <li>Battery Storage</li>
      <li>LED Lighting</li>
      <li>Energy Saving Solutions</li>
    </ul>
  </section>
</body>
</html>
```